co working space / serviced office/ business centre

Brevlo - brevlo.in, is a very young brand bieng run by 3 young entrepreneurs. We want to be become out of the league company delivering fabulous and beautiful serviced offices in India and abroad. We hire designers who have made spaces across the world. We want to get visiting card design which gives complete fresh look to the people who carries that card, has to be very impactful and should symbolise happy young and energetic brand. should be completely out of the box thinking of international level, should portray global brand image.

Target Market(s)

Startups, (Small, medium and large corporates)

Industry/Entity Type

Business

Contact Information for Business Card

Name, Email, Address, Mobile number, Landline number, website

Colors

Designer to choose colors to be used in the design.

Requirements
Must have
• Nice new shape
Nice to have
• We want creative cuts, different size and impactful brand clarity
Should not have
• Boring and regular design and shape

```html
<!DOCTYPE html>
<html lang="en">
<head>
<meta charset="utf-8">
<title>Brevlo Business Card</title>
<link href="https://fonts.googleapis.com/css2?family=Work+Sans:wght@400;500;700&display=swap" rel="stylesheet">
<style>
  :root {
    --brand-red: #ed1c24;
    --ink: #2b2b2b;
    --band: #1a1a1a;
    --paper: #ffffff;
    --backdrop: #ececec;
  }
  * { margin: 0; padding: 0; box-sizing: border-box; }
  html, body { width: 1200px; height: 930px; overflow: hidden; }
  body {
    background: var(--backdrop);
    font-family: "Work Sans", sans-serif;
    position: relative;
  }
  .card {
    position: absolute;
    left: 278px;
    width: 644px;
    height: 368px;
    border-radius: 24px;
    overflow: hidden;
    box-shadow: 0 8px 22px rgba(0,0,0,0.18);
  }
  .card--front { top: 76px; background: var(--paper); }
  .card--back { top: 486px; background: var(--brand-red); }

  .brand-block {
    position: absolute;
    text-align: center;
  }
  .card--front .brand-block { left: 50px; width: 294px; top: 138px; color: var(--brand-red); }
  .card--back .brand-block { left: 160px; width: 324px; top: 138px; color: var(--paper); }

  .brand-name {
    display: inline-flex;
    align-items: center;
    gap: 12px;
    font-weight: 700;
    letter-spacing: 2px;
    line-height: 1;
  }
  .card--front .brand-name { font-size: 50px; }
  .card--back .brand-name { font-size: 54px; }
  .brand-square {
    display: inline-block;
    width: 18px;
    height: 18px;
    background: currentColor;
  }
  .tagline {
    font-weight: 700;
    font-size: 14px;
    letter-spacing: 3px;
    margin-top: 16px;
    line-height: 1;
  }

  .divider {
    position: absolute;
    left: 380px;
    top: 92px;
    width: 2px;
    height: 170px;
    background: var(--ink);
  }
  .contact {
    position: absolute;
    left: 409px;
    top: 100px;
    color: var(--ink);
  }
  .contact__name {
    color: var(--brand-red);
    font-weight: 700;
    font-size: 26px;
    line-height: 1;
    letter-spacing: 0.3px;
  }
  .contact__role { font-size: 15px; margin-top: 5px; }
  .contact__address { font-size: 15px; line-height: 20px; margin-top: 6px; }
  .contact__list { list-style: none; margin-top: 5px; }
  .contact__list li {
    display: flex;
    align-items: center;
    font-size: 15px;
    line-height: 20px;
  }
  .contact__list svg { width: 11px; height: 11px; margin-right: 12px; margin-left: 2px; }

  .band {
    position: absolute;
    left: 0; right: 0; bottom: 0;
    height: 32px;
    background: var(--band);
  }
</style>
</head>
<body>
  <section class="card card--front">
    <div class="brand-block">
      <div class="brand-name"><span class="brand-square"></span>BREVLO</div>
      <div class="tagline">WORK. MEET. GROW</div>
    </div>

    <div class="divider"></div>

    <div class="contact">
      <div class="contact__name">AARAV MEHTA</div>
      <div class="contact__role">Director</div>
      <div class="contact__address">418 Linden Park<br>Road Pune, MH 411045</div>
      <ul class="contact__list">
        <li>
          <svg viewBox="0 0 12 12"><path d="M3 1 L5 3.5 L4 5 Q5 7 7 8 L8.5 7 L11 9 L9.5 11 Q4 10.5 1 3 Z" fill="none" stroke="#ed1c24" stroke-width="1.2"/></svg>
          020 415 2870
        </li>
        <li>
          <svg viewBox="0 0 12 12"><rect x="3" y="1" width="6" height="10" rx="1" fill="none" stroke="#ed1c24" stroke-width="1.3"/><line x1="5" y1="9" x2="7" y2="9" stroke="#ed1c24" stroke-width="1"/></svg>
          987 220 4613
        </li>
        <li>
          <svg viewBox="0 0 12 12"><rect x="1" y="2.5" width="10" height="7" fill="none" stroke="#ed1c24" stroke-width="1.2"/><path d="M1 2.5 L6 6.5 L11 2.5" fill="none" stroke="#ed1c24" stroke-width="1.2"/></svg>
          info@brevlo.in
        </li>
        <li>
          <svg viewBox="0 0 12 12"><circle cx="6" cy="6" r="5" fill="none" stroke="#ed1c24" stroke-width="1"/><ellipse cx="6" cy="6" rx="2.2" ry="5" fill="none" stroke="#ed1c24" stroke-width="0.9"/><line x1="1" y1="6" x2="11" y2="6" stroke="#ed1c24" stroke-width="0.9"/></svg>
          www.brevlo.in
        </li>
      </ul>
    </div>

    <div class="band"></div>
  </section>

  <section class="card card--back">
    <div class="brand-block">
      <div class="brand-name"><span class="brand-square"></span>BREVLO</div>
      <div class="tagline">WORK. MEET. GROW</div>
    </div>
  </section>
</body>
</html>
```